Commercial/Corporate Law Firm needs Website Design

Hi guys. I've started up a new law firm and would love your help designing an attractive website. I'll need both design and coding, and to make it easy for us to edit as necessary later, I think it should be built off a Wordpress.org structure.
FIRST IMPRESSIONS
It's very important that the first impression of the website really captures our prospective clients' attention and impresses them. Their first three seconds needs to be good.
I imagine the homepage may be short, with a menu bar and a compelling image, and with a tagline overlaid or underneath (eg. "It's about results.")
The image should be related to our practice areas: eg. IPOs, corporate transactions, or commercial negotiations.
I have previously suggested there could be a skyline image of Sydney or Adelaide. However, because we are based in Adelaide, I don't think Sydney is appropriate - and Adelaide is probably too boring to use.
HOMEPAGE
Being a new firm, we don't have many existing testimonials, and I will be the only lawyer to start with. So we need to focus on the nature of the services we will provide and how my experience can help them. We have an existing logo to use, and I would like the website colour scheme not to clash with that logo (dark blue and white).
After the initial image and tagline there should be a brief introduction to each of the main areas of work, eg. "We specialise in three main areas of practice:"
1. Corporate Transactions and Regulation
2. Business Law and Dispute Resolution
3. Migration Assistance
These should each have an appropriate photo and link to a separate page that briefly describes our services in that area.
Below that there should be a message from me with a photo. Finally, at the bottom, there should be a "Contact Us" section which shows a Google image of our address, contact details, and then our logo with colours inverted.
OTHER PAGES
While we will need some other pages, they should all be fairly simple. I think we will need one page to say "About Us", where I will put information about my experience. I think we will then need one page for each of the 3 areas listed above, which just needs an appropriate image and then text to describe the service. Finally, a "Contact Us" page which I imagine will be the same as the bottom of the homepage.
OTHER DETAILS
For now you can use details from my LinkedIn page to fill out any other text as necessary, or the photo.
Because the logo is square, I would prefer the design of the website also to be rectangular.
Looking forward to seeing your work! Thank you.
Marcus
Potential clients:
Businesses with legal issues or disputes
Companies wishing to list on the stock market

```html
<!DOCTYPE html>
<html lang="en">
<head>
<meta charset="utf-8">
<title>Calloway Legal</title>
<link rel="stylesheet" href="https://fonts.googleapis.com/css2?family=Libre+Baskerville&family=Lato:wght@400&family=Open+Sans:ital,wght@0,400;1,400&display=swap">
<style>
  :root {
    --navy: #1b3361;
    --navy-deep: #162b54;
    --navy-mid: #2a4a80;
    --page: #f6f6f6;
    --white: #ffffff;
    --grey-text: #9a9a9a;
    --body-text: #555555;
    --bubble: #8c8c8c;
    --frame: #6f6f6f;
    --hero-text: #b9c3d6;
  }
  * { box-sizing: border-box; margin: 0; padding: 0; }
  html, body { width: 1200px; height: 2381px; overflow: hidden; background: var(--page); }
  body { font-family: "Open Sans", sans-serif; color: var(--body-text); }
  .page { position: relative; width: 1200px; height: 2381px; overflow: hidden; }
  .abs { position: absolute; }
  .serif { font-family: "Libre Baskerville", serif; font-weight: 400; }

  /* Hero */
  .hero { left: 0; top: 0; width: 1200px; height: 678px;
    background: linear-gradient(160deg, #2d4f86 0%, #1d3a6d 45%, #2f5793 75%, #1a3464 100%); }
  .hero-brand { left: 0; width: 1200px; text-align: center; top: 88px; }
  .brand-square { display: inline-block; width: 104px; height: 104px; border: 3px solid var(--white); }
  .brand-name { margin-top: 30px; font-size: 40px; letter-spacing: 4px; color: var(--white); }
  .hero-title { left: 0; width: 1200px; top: 325px; text-align: center; font-size: 76px; color: var(--white); letter-spacing: 1px; }
  .hero-lead { left: 300px; width: 600px; top: 422px; text-align: center; font-family: "Lato", sans-serif; font-size: 21px; line-height: 28px; color: var(--hero-text); }

  /* Nav */
  .main-nav { left: 0; top: 678px; width: 1200px; height: 62px; background: var(--navy); }
  .nav-item { top: 21px; font-size: 17px; color: #9aa8c2; display: flex; align-items: center; gap: 6px; letter-spacing: 0.3px; }
  .nav-item .mark { width: 18px; height: 18px; background: #8593ad; }
  .nav-item.active { color: var(--white); }
  .nav-item.active .mark { background: var(--white); }

  /* Services */
  .section-title { font-size: 38px; color: var(--navy); letter-spacing: 1px; }
  .services-title { left: 0; width: 1200px; text-align: center; top: 800px; }
  .brand-panel { left: 111px; top: 884px; width: 311px; height: 309px; border: 4px solid var(--frame); padding: 10px; }
  .brand-panel-inner { width: 100%; height: 100%; background: var(--navy); display: flex; align-items: center; justify-content: center; }
  .brand-panel-inner span { color: var(--white); font-size: 26px; letter-spacing: 3px; }
  .service-icon { width: 115px; height: 114px; background: var(--navy); outline: 2px solid var(--navy); outline-offset: 3px; border: 2px solid var(--white); display: flex; align-items: center; justify-content: center; }
  .service-name { font-size: 22px; color: #333; }
  .service-desc { font-size: 15px; line-height: 23px; color: var(--grey-text); width: 300px; }

  /* Quote */
  .quote-photo { left: 450px; top: 1312px; width: 750px; height: 397px;
    background: linear-gradient(100deg, #cfcfcf 0%, #b8b8b8 40%, #dcdcdc 75%, #c4c4c4 100%); }
  .quote-band { left: 0; top: 0; }
  .quote-title { left: 120px; width: 388px; top: 1444px; text-align: right; font-size: 41px; color: var(--white); letter-spacing: 1px; }
  .quote-lead { left: 200px; width: 308px; top: 1514px; text-align: right; font-size: 15.5px; line-height: 21px; color: var(--white); }
  .mail-badge { left: 540px; top: 1451px; width: 120px; height: 120px; border-radius: 50%; background: #c8c8c8; border: 6px solid var(--white); display: flex; align-items: center; justify-content: center; }
  .field { left: 741px; width: 332px; background: var(--white); border: 1px solid #d8d8d8; border-radius: 3px; font-family: Arial, sans-serif; font-size: 14px; color: #555; padding: 10px 16px; }
  .btn { background: var(--navy); color: var(--white); border: 2px solid #0f2040; border-radius: 3px; box-shadow: 0 2px 3px rgba(0,0,0,0.35); font-family: "Lato", sans-serif; letter-spacing: 1px; display: flex; align-items: center; justify-content: center; }
  .submit-btn { left: 741px; top: 1611px; width: 143px; height: 49px; font-size: 22px; }

  /* About & testimonials */
  .about-title { left: 79px; top: 1780px; }
  .about-text { left: 79px; top: 1839px; width: 660px; font-size: 15.5px; line-height: 23px; color: var(--body-text); }
  .learn-btn { left: 78px; top: 1976px; width: 185px; height: 50px; font-size: 20px; }
  .testimonials-title { left: 814px; top: 1780px; }
  .bubble { left: 811px; top: 1844px; width: 311px; height: 135px; background: var(--bubble); border-radius: 4px; padding: 22px 14px; font-size: 14px; line-height: 21px; font-style: italic; color: var(--white); }
  .bubble-tail { left: 844px; top: 1978px; }
  .author { left: 823px; top: 2000px; font-size: 15px; color: var(--navy); }
  .author-role { left: 823px; top: 2024px; font-size: 14px; font-style: italic; color: #777; }

  /* Footer */
  .site-footer { left: 0; top: 2089px; width: 1200px; height: 292px; background: var(--navy); color: var(--white); }
  .footer-heading { top: 41px; font-size: 18px; letter-spacing: 1px; color: var(--white); }
  .footer-text { font-size: 14px; line-height: 20px; color: var(--white); }
  .footer-row { display: flex; gap: 12px; align-items: flex-start; }
  .footer-links { left: 344px; top: 79px; list-style: none; font-size: 14px; line-height: 31px; }
  .post { left: 608px; display: flex; gap: 10px; }
  .post-thumb { width: 54px; height: 54px; border-radius: 50%; border: 3px solid var(--white); background: linear-gradient(135deg, #e9e2d6, #b7a58c); }
  .post-text { font-size: 14px; line-height: 18px; width: 180px; }
  .post-date { font-size: 11.5px; }
  .footer-brand { left: 895px; width: 180px; top: 36px; text-align: center; }
  .footer-brand .sq { display: inline-block; width: 54px; height: 54px; border: 2px solid var(--white); background: #8593ad; }
  .footer-brand .name { margin-top: 8px; font-size: 19px; letter-spacing: 2px; color: var(--white); }
  .social { display: flex; justify-content: center; gap: 6px; margin-top: 12px; }
  .social span { width: 40px; height: 40px; border-radius: 50%; border: 1.5px solid #8f9fbf; }
  .social span:first-child { background: var(--white); border-color: var(--white); }
  .footer-rule { left: 79px; top: 241px; width: 1044px; height: 1px; background: #4a6290; }
  .copyright { left: 0; width: 1200px; top: 256px; text-align: center; font-size: 14px; }
</style>
</head>
<body>
<div class="page">

  <header>
    <div class="abs hero" role="img" aria-label="Upward view of glass office towers against a cloudy sky, tinted blue"></div>
    <div class="abs hero-brand">
      <span class="brand-square"></span>
      <div class="brand-name serif">CALLOWAY LEGAL</div>
    </div>
    <h1 class="abs hero-title serif">WE GET RESULTS</h1>
    <p class="abs hero-lead">Lorem Ipsum is simply dummy text of the printing and typesetting industry. Lorem Ipsum has been the industry's standard dummy.</p>

    <nav class="abs main-nav">
      <a class="abs nav-item active" style="left:206px"><span class="mark"></span>HOME</a>
      <a class="abs nav-item" style="left:397px"><span class="mark"></span>ABOUT</a>
      <a class="abs nav-item" style="left:606px"><span class="mark"></span>PRACTICE AREAS</a>
      <a class="abs nav-item" style="left:887px"><span class="mark"></span>CONTACT</a>
    </nav>
  </header>

  <section class="services">
    <h2 class="abs section-title services-title serif">OUR SERVICES</h2>
    <div class="abs brand-panel"><div class="brand-panel-inner"><span class="serif">CALLOWAY LEGAL</span></div></div>

    <div class="abs service-icon" style="left:444px;top:862px">
      <svg width="64" height="64" viewBox="0 0 64 64" fill="none" stroke="#fff" stroke-width="4">
        <circle cx="32" cy="32" r="11"/><path d="M16 6v40M8 38l8 8 8-8M48 58V18M40 26l8-8 8 8"/>
      </svg>
    </div>
    <h3 class="abs service-name serif" style="left:582px;top:884px">Corporate Transactions and Regulation</h3>
    <p class="abs service-desc" style="left:582px;top:912px">Lorem Ipsum is simply dummy text of the printing and typesetting industry.</p>

    <div class="abs service-icon" style="left:559px;top:998px">
      <svg width="70" height="40" viewBox="0 0 70 40" fill="none" stroke="#fff" stroke-width="4" stroke-linecap="round">
        <path d="M4 10h14l10 6M66 10H52L38 18l-8 4M22 26l10 8 8-4 10-6"/>
      </svg>
    </div>
    <h3 class="abs service-name serif" style="left:697px;top:1019px">Business Law and Dispute Resolution</h3>
    <p class="abs service-desc" style="left:697px;top:1047px">Lorem Ipsum is simply dummy text of the printing and typesetting industry.</p>

    <div class="abs service-icon" style="left:444px;top:1122px">
      <svg width="64" height="60" viewBox="0 0 64 60" fill="none" stroke="#fff" stroke-width="4">
        <path d="M30 6h26v48H30M4 22h32M28 14l8 8-8 8M4 38h32M28 30l8 8-8 8"/>
      </svg>
    </div>
    <h3 class="abs service-name serif" style="left:582px;top:1144px">Migration Assistance</h3>
    <p class="abs service-desc" style="left:582px;top:1172px">Lorem Ipsum is simply dummy text of the printing and typesetting industry.</p>
  </section>

  <section class="quote">
    <div class="abs quote-photo" role="img" aria-label="Greyscale photo of a smiling man working at a laptop in an office"></div>
    <svg class="abs quote-band" width="1200" height="2381" viewBox="0 0 1200 2381">
      <polygon points="78,1303 683,1303 505,1719 78,1719" fill="var(--navy)"/>
    </svg>
    <h2 class="abs quote-title serif">GET A QUOTE</h2>
    <p class="abs quote-lead">Lorem Ipsum is simply dummy text of the printing and typesetting industry. Lorem Ipsum has been the industry.</p>
    <div class="abs mail-badge">
      <svg width="50" height="34" viewBox="0 0 50 34" fill="#fff" stroke="#c8c8c8" stroke-width="2">
        <rect x="1" y="1" width="48" height="32"/><path d="M1 1l24 18L49 1" fill="none"/>
      </svg>
    </div>
    <div class="abs field" style="top:1360px;height:44px">Name</div>
    <div class="abs field" style="top:1412px;height:45px">Phone</div>
    <div class="abs field" style="top:1463px;height:45px">E-Mail</div>
    <div class="abs field" style="top:1517px;height:80px">Message</div>
    <div class="abs btn submit-btn">SUBMIT</div>
  </section>

  <section class="about">
    <h2 class="abs section-title about-title serif">ABOUT US</h2>
    <p class="abs about-text">Lorem Ipsum is simply dummy text of the printing and typesetting industry. Lorem Ipsum has been the industry's standard dummy text ever since the 1500s, when an unknown printer took a galley of type and scrambled it to make a type specimen book. It has survived not only five centuries, but also the leap into electronic typesetting, remaining essentially unchanged. It was popularised in the 1960s with the release of Letraset sheets containing.</p>
    <div class="abs btn learn-btn">LEARN MORE</div>
  </section>

  <section class="testimonials">
    <h2 class="abs section-title testimonials-title serif">TESTIMONIALS</h2>
    <blockquote class="abs bubble">"Lorem Ipsum is simply dummy text of the printing and typesetting industry. Lorem Ipsum has been the industry's standard dummy text ever since the 1500s."</blockquote>
    <svg class="abs bubble-tail" width="16" height="14" viewBox="0 0 16 14"><polygon points="0,0 14,0 0,13" fill="var(--bubble)"/></svg>
    <p class="abs author serif">Lorem ipsum</p>
    <p class="abs author-role">CEO</p>
  </section>

  <footer class="abs site-footer">
    <h4 class="abs footer-heading serif" style="left:79px">CONTACT INFO</h4>
    <div class="abs footer-row footer-text" style="left:79px;top:76px">
      <svg width="20" height="18" viewBox="0 0 20 18" fill="none" stroke="#fff" stroke-width="1.6"><path d="M1 3l6-2 6 2 6-2v14l-6 2-6-2-6 2zM7 1v14M13 3v14"/></svg>
      <span style="width:200px">123 Building Name, Street Name, Area, city, Country - zipcode</span>
    </div>
    <div class="abs footer-row footer-text" style="left:79px;top:158px">
      <svg width="20" height="20" viewBox="0 0 20 20" fill="none" stroke="#fff" stroke-width="1.6"><path d="M4 1l4 4-2 3c1 2 4 5 6 6l3-2 4 4-3 3C9 19 1 11 1 4z"/></svg>
      <span>123-4567-890</span>
    </div>
    <div class="abs footer-row footer-text" style="left:79px;top:194px">
      <svg width="20" height="16" viewBox="0 0 20 16" fill="none" stroke="#fff" stroke-width="1.6"><rect x="1" y="1" width="18" height="14"/><path d="M1 1l9 7 9-7"/></svg>
      <span>info@callowaylegal.com</span>
    </div>

    <h4 class="abs footer-heading serif" style="left:344px">USEFUL LINKS</h4>
    <ul class="abs footer-links">
      <li>Home</li><li>About Us</li><li>Practice Area</li><li>Contact Us</li>
    </ul>

    <h4 class="abs footer-heading serif" style="left:611px;letter-spacing:0">Blog Post</h4>
    <div class="abs post" style="top:74px">
      <div class="post-thumb" role="img" aria-label="Blog post thumbnail photo"></div>
      <div class="post-text">Lorem Ipsum is simply dummy text of<br><span class="post-date">Today 5:60 pm - 08.06.2016</span></div>
    </div>
    <div class="abs post" style="top:146px">
      <div class="post-thumb" role="img" aria-label="Blog post thumbnail photo"></div>
      <div class="post-text">Lorem Ipsum is simply dummy text of<br><span class="post-date">Today 2:10 pm - 08.06.2016</span></div>
    </div>

    <div class="abs footer-brand">
      <span class="sq"></span>
      <div class="name serif">CALLOWAY LEGAL</div>
      <div class="social" aria-label="Social links"><span></span><span></span><span></span></div>
    </div>

    <div class="abs footer-rule"></div>
    <p class="abs copyright">© <span class="serif">CALLOWAY LEGAL</span> - 2018. All Rights Reserved.</p>
  </footer>

</div>
</body>
</html>
```